Las Vegas transportation company needs a dynamic design for business cards

We are a transportation management company based in Las Vegas specializing in operating and maintaining public transit systems. We want to keep our existing logo but would like to design business cards that feature one or more transit systems (e.g. monorail, train, bus) and maybe also the Las Vegas landscape.

```html
<!DOCTYPE html>
<html lang="en">
<head>
<meta charset="utf-8">
<title>Meridian Transit Group – Business Card</title>
<link href="https://fonts.googleapis.com/css2?family=Cinzel:wght@400&family=Arimo:wght@400&display=swap" rel="stylesheet">
<style>
  :root {
    --page-bg: #1c1c1e;
    --card-black: #0b0b0c;
    --divider: #2a2a2e;
    --brand-blue: #3550a8;
    --name-blue: #6f93e6;
    --link-blue: #5b86e8;
    --text-light: #e9e9ec;
    --bus-tone: #9a3350;
    --sky-tone: #7fa6d9;
    --rail-tone: #6d8fb4;
    --city-dark: #17120c;
    --city-glow: #a07a3a;
  }
  * { box-sizing: border-box; margin: 0; padding: 0; }
  html, body { width: 1200px; height: 900px; overflow: hidden; }
  body {
    background: var(--page-bg);
    display: flex;
    flex-direction: column;
    align-items: center;
    justify-content: center;
    gap: 48px;
  }
  .card {
    width: 630px;
    height: 360px;
    position: relative;
    overflow: hidden;
    border-radius: 2px;
  }
  /* Front side */
  .card-front {
    background: var(--card-black);
    display: grid;
    grid-template-columns: 46% 54%;
  }
  .brand-panel {
    display: flex;
    flex-direction: column;
    align-items: center;
    justify-content: center;
    gap: 10px;
    border-right: 1px solid var(--divider);
  }
  .brand-mark {
    width: 16px; height: 16px;
    background: var(--brand-blue);
  }
  .brand-name {
    font-family: "Cinzel", serif;
    font-weight: 400;
    color: var(--brand-blue);
    font-size: 30px;
    letter-spacing: 2px;
    text-align: center;
    line-height: 1.15;
  }
  .contact-panel {
    padding: 70px 0 0 34px;
    font-family: "Arimo", sans-serif;
    color: var(--text-light);
  }
  .person-name {
    font-family: "Cinzel", serif;
    font-weight: 400;
    color: var(--name-blue);
    font-size: 26px;
    letter-spacing: 1px;
  }
  .person-title { font-size: 16px; margin-top: 2px; margin-bottom: 22px; }
  .contact-list { list-style: none; font-size: 16px; line-height: 1.6; }
  .contact-list li { display: flex; align-items: center; gap: 9px; }
  .contact-list svg { width: 15px; height: 15px; flex: none; }
  .accent { color: var(--link-blue); }
  .address { margin-top: 18px; font-size: 16px; line-height: 1.45; }
  /* Back side */
  .card-back {
    background: #050505;
    display: grid;
    grid-template-columns: 1fr 1fr 1fr;
    grid-template-rows: 44% 56%;
    gap: 3px;
  }
  .photo { width: 100%; height: 100%; }
  .photo-bus { background: linear-gradient(160deg, var(--sky-tone) 0%, var(--bus-tone) 55%, #5a2434 100%); }
  .photo-monorail { background: linear-gradient(150deg, var(--sky-tone) 0%, #c9ced6 55%, #7a8290 100%); }
  .photo-train { background: linear-gradient(150deg, #8fb9e6 0%, var(--rail-tone) 45%, #c2703a 75%, #4c6a5a 100%); }
  .photo-skyline {
    grid-column: 1 / 4;
    background: radial-gradient(ellipse at 60% 40%, var(--city-glow) 0%, #4a3620 35%, var(--city-dark) 75%);
  }
</style>
</head>
<body>

  <section class="card card-front">
    <div class="brand-panel">
      <span class="brand-mark"></span>
      <div class="brand-name">MERIDIAN<br>TRANSIT GROUP</div>
    </div>
    <div class="contact-panel">
      <h1 class="person-name">DANIEL HARTLEY</h1>
      <p class="person-title">Managing Director</p>
      <ul class="contact-list">
        <li>
          <svg viewBox="0 0 16 16" aria-hidden="true"><path d="M4 1.5l2.2 3-1.3 1.6c.9 1.9 2.3 3.3 4.2 4.2l1.6-1.3 3 2.2-1.4 2.6C7.2 13.6 2.4 8.8 1.4 3z" fill="var(--name-blue)"/></svg>
          044-555 218 604
        </li>
        <li>
          <svg viewBox="0 0 16 16" aria-hidden="true"><rect x="1" y="3" width="14" height="10" fill="var(--name-blue)"/><path d="M1 3l7 6 7-6" stroke="var(--card-black)" stroke-width="1.3" fill="none"/></svg>
          hello@meridiantg.com
        </li>
        <li>
          <svg viewBox="0 0 16 16" aria-hidden="true"><g fill="none" stroke="var(--name-blue)" stroke-width="1.3"><circle cx="8" cy="8" r="6.5"/><ellipse cx="8" cy="8" rx="2.8" ry="6.5"/><path d="M1.5 8h13M2.5 4.8h11M2.5 11.2h11"/></g></svg>
          <span>www.<span class="accent">meridiantg</span>.com</span>
        </li>
      </ul>
      <p class="address">1180 Desert Line Avenue<br>89101, United States</p>
    </div>
  </section>

  <section class="card card-back">
    <div class="photo photo-bus" role="img" aria-label="Photo of a red double-decker city bus"></div>
    <div class="photo photo-monorail" role="img" aria-label="Photo of a monorail train on an elevated track"></div>
    <div class="photo photo-train" role="img" aria-label="Photo of a diesel locomotive on a railway line"></div>
    <div class="photo photo-skyline" role="img" aria-label="Night photo of the Las Vegas Strip skyline with illuminated hotels"></div>
  </section>

</body>
</html>
```